Quick Straightforward Billboard Redesign

- Design billboard sized for 10 foot' x 36' foot width live area size and please include bleeds 6" around all sides
- Exact blue color match is imperative in headline, logo, phone number bubble or wherever used. C-83 / M-45 / Y-1 / K-0-
- What I hope to illustrate is that our company offers the best porch screening in the area area, in regards to quality, expertise, durability, storms proof, but we do not build screen porches.
- Current board is attached below from previous designer, and as you can see sizing was off, white space on edges make it appear to be sized incorrectly.
- I also attached my own little mock up idea well well if it helps, favorite image, logo, headline, etc and ideas perhaps on expanding or making this better?

Thanks so much!

Target Market(s)

Drivers and passengers, Southeastern NC, are of immense new construction and high end homes.

Industry/Entity Type

Construction

Colors
0054AA
0677BA
7BADD7
CADEEF
E8F1F8

Requirements
Must have
• Blue color matching
Nice to have
• Design spins or other thoughts on my little mock up

```html
<!DOCTYPE html>
<html lang="en">
<head>
<meta charset="UTF-8">
<title>Harborline Screens Billboard</title>
<link href="https://fonts.googleapis.com/css2?family=Oswald:wght@500;600&family=Montserrat:wght@700&display=swap" rel="stylesheet">
<style>
  :root {
    --brand-blue: #0568b3;
    --brand-green: #00b55a;
    --paper: #ffffff;
    --stage: #e9eef3;
    --ceiling: #eef0f1;
    --sky: #6aa8e2;
    --lake: #9cc0dd;
    --lawn: #8fb75a;
    --wicker: #6b5a4a;
    --stone: #cfc8bd;
  }
  * { margin: 0; padding: 0; box-sizing: border-box; }
  html, body {
    width: 1200px;
    height: 800px;
    overflow: hidden;
    background: var(--stage);
  }
  .billboard {
    position: absolute;
    left: 0;
    top: 233px;
    width: 1200px;
    height: 333px;
    background: var(--paper);
    overflow: hidden;
  }
  .headline {
    position: absolute;
    left: 26px;
    font-family: "Oswald", sans-serif;
    font-weight: 600;
    line-height: 1;
    white-space: nowrap;
  }
  .headline--primary {
    top: 14px;
    font-size: 90px;
    color: var(--brand-blue);
    letter-spacing: -1px;
  }
  .headline--secondary {
    top: 108px;
    font-size: 70px;
    color: var(--brand-green);
    letter-spacing: -0.5px;
  }
  .brand {
    position: absolute;
    left: 26px;
    top: 194px;
    display: flex;
    align-items: center;
    gap: 14px;
  }
  .brand__mark {
    width: 40px;
    height: 40px;
    background: var(--brand-blue);
  }
  .brand__name {
    font-family: "Oswald", sans-serif;
    font-weight: 500;
    font-size: 44px;
    line-height: 1;
    color: var(--brand-blue);
    text-transform: uppercase;
    white-space: nowrap;
  }
  .phone-band {
    position: absolute;
    left: 0;
    bottom: 0;
    width: 645px;
    height: 82px;
    background: var(--brand-blue);
    display: flex;
    align-items: center;
    padding-left: 22px;
  }
  .phone-band__number {
    font-family: "Montserrat", sans-serif;
    font-weight: 700;
    font-size: 66px;
    line-height: 1;
    color: var(--paper);
    letter-spacing: 1px;
  }
  .photo-divider {
    position: absolute;
    left: 722px;
    top: 0;
    width: 14px;
    height: 333px;
    background: var(--brand-green);
  }
  .porch-photo {
    position: absolute;
    left: 736px;
    top: 0;
    width: 464px;
    height: 333px;
    background: linear-gradient(180deg,
      var(--ceiling) 0%,
      var(--ceiling) 42%,
      var(--sky) 50%,
      var(--lake) 60%,
      var(--lawn) 68%,
      var(--wicker) 82%,
      var(--stone) 100%);
  }
</style>
</head>
<body>
  <section class="billboard">
    <h1 class="headline headline--primary">Screen Your Porch.</h1>
    <p class="headline headline--secondary">Built for the Coast.</p>
    <div class="brand">
      <span class="brand__mark"></span>
      <span class="brand__name">Harborline Screens</span>
    </div>
    <div class="phone-band">
      <span class="phone-band__number">910.555.0142</span>
    </div>
    <div class="photo-divider"></div>
    <div class="porch-photo" role="img" aria-label="Screened porch with white ceiling, fan, wicker chairs and a potted palm overlooking a lawn and lake"></div>
  </section>
</body>
</html>
```